Wine Label for a Sweet Wine Called "Glimmo"

We need a wine label that will be used for both a sweet red and a sweet white wine. The very important thing to remember is the target market for these wines is: young American women who love sweet wines and they also spend a lot of their money on their hair, clothes, jewelry, nails. They LOVE Glimmo (Glimmo is a word used to describe flashy accessories, jewelry, decoration.) This label needs to be eye catching, showy, fun, glittery. Please put the brand name, "Glimmo," big, and then in smaller but still readable words underneath the label or somewhere on the label: Sweet, Sophisticated, Red (or white). (An example of what I mean is attached). To differentiate between the two color wines you can suggest color changes to differentiate between the red label and the white label but the label design itself should be the same. Ultimately, the label can be the exact same label for both white and red as long as it looks good on a white wine (a greenish/yellow wine in a clear glass bottle) and a red wine (a dark color wine in a dark bottle).

I've attached an example of the text size relationship between the word Glimmo and the words to go underneath or elsewhere on the label, but you can certainly play with this-- it is just a suggestion of the text size relationship, and definitely NOT at all mandatory that you use any of these fonts.

You can pick the size of the label but try to stay within normal wine label sizes, meaning don't go bigger than approx. 3.5 inches wide and 5 inches tall.

Target Market(s)

Young American women who love sweet wines and spend a lot of money on their hair, clothes, jewelry, nails. They love Glimmo (Glimmo is a word that means flashy accessories, jewelry, decoration)

Requirements
Must have
• It needs to be flashy, glittery, fun, eye catching, memorable
Nice to have
• It shouldn't be too too ultra feminine! The target market is strong independent women and we also have men who will buy it too.

```html
<!DOCTYPE html>
<html lang="en">
<head>
<meta charset="utf-8">
<title>Glimmo – Sweet Red and Sweet White Labels</title>
<link rel="stylesheet" href="https://fonts.googleapis.com/css2?family=Allura&family=Josefin+Sans:wght@300;400&display=swap">
<style>
  :root {
    --backdrop: #eeeeee;
    --backdrop-glow: #fafafa;
    --red-base: #e25a6b;
    --red-deep: #c63a52;
    --red-glow: #f4a6ae;
    --white-base: #b5bf86;
    --white-deep: #7c8c4c;
    --white-glow: #e2e6bd;
    --label-ink: #fbf3f1;
    --frame-line: rgba(255, 255, 255, 0.7);
  }
  * { margin: 0; padding: 0; box-sizing: border-box; }
  html, body {
    width: 1200px;
    height: 1000px;
    overflow: hidden;
  }
  body {
    position: relative;
    background: radial-gradient(ellipse at 50% 40%, var(--backdrop-glow) 0%, var(--backdrop) 75%);
  }
  .label {
    position: absolute;
    top: 198px;
    width: 249px;
    height: 354px;
    overflow: hidden;
    color: var(--label-ink);
  }
  .label--red { left: 93px; background: var(--red-base); }
  .label--white { left: 857px; background: var(--white-base); }

  .label__swirl {
    position: absolute;
    inset: 0;
  }
  .label--red .label__swirl {
    background:
      radial-gradient(ellipse 40% 22% at 46% 52%, var(--red-glow) 0%, rgba(244,166,174,0) 100%),
      radial-gradient(ellipse 70% 40% at 50% 42%, var(--red-deep) 0%, rgba(198,58,82,0) 100%),
      var(--red-base);
  }
  .label--white .label__swirl {
    background:
      radial-gradient(ellipse 40% 22% at 46% 54%, var(--white-glow) 0%, rgba(226,230,189,0) 100%),
      radial-gradient(ellipse 70% 40% at 44% 40%, var(--white-deep) 0%, rgba(124,140,76,0) 100%),
      var(--white-base);
  }
  .label__frame {
    position: absolute;
    inset: 7px;
    border: 1px solid var(--frame-line);
  }
  .label__brand {
    position: absolute;
    left: 14px;
    right: 14px;
    top: 150px;
    text-align: center;
    white-space: nowrap;
    font-family: "Allura", cursive;
    font-size: 74px;
    line-height: 1;
    font-weight: 400;
  }
  .label__tagline {
    position: absolute;
    left: 0;
    right: 0;
    top: 296px;
    text-align: center;
    white-space: nowrap;
    font-family: "Josefin Sans", sans-serif;
    font-weight: 300;
    font-size: 9px;
    letter-spacing: 1.8px;
    text-transform: uppercase;
  }
</style>
</head>
<body>
  <section class="label label--red" aria-label="Glimmo sweet red label">
    <div class="label__swirl" role="img" aria-label="Glossy swirling rose-red pattern with a soft light centre"></div>
    <div class="label__frame"></div>
    <h1 class="label__brand">Glimmo</h1>
    <p class="label__tagline">Sweet | Red | Sophisticated</p>
  </section>

  <section class="label label--white" aria-label="Glimmo sweet white label">
    <div class="label__swirl" role="img" aria-label="Glossy swirling olive-green pattern with a soft light centre"></div>
    <div class="label__frame"></div>
    <h2 class="label__brand">Glimmo</h2>
    <p class="label__tagline">Sweet | White | Sophisticated</p>
  </section>
</body>
</html>
```